Human Resource Consulting practice needs a business card design

We need a business card design (double sided colour) for our Human Resource (HR) consulting practice in regional New South Wales, australia. Our business name is Staff Compass. We support small and medium business across the Mid North Coast of New South Wales by providing them with outsourced HR support, services and products to help them achieve compliance with workplace legislation and across all areas of the employment lifecycle from recruitment to termination and everything in between. Our corporate colours are hot pink and black. The final design should communicate professionalism, trust, people focus.
I have attached the current (old) business card for your reference.

Target Market(s)

Business owners and high level managers

Industry/Entity Type

Business

Contact Information for Business Card

Name
Title
Phone no
Mobile no
Address
PO Box
email address
website

Colors
e34197

Requirements
Must have
• Tempate for changing business card personal details including Name, position title, mobile number, email address.
• Keep current logo and colours as per attached
• Logo must be presented in 2 colours or black only not white
Nice to have
• One side logo and graphic only other side logo and personal details
Should not have
• Should not be the same as the current version (attached) but a modern interpretation.
• Does not need a busy reverse side with our list of services as per current version. I feel this is too busy.
• No photos

```html
<!DOCTYPE html>
<html lang="en">
<head>
<meta charset="utf-8">
<title>Staff Compass – Business Card</title>
<link rel="stylesheet" href="https://fonts.googleapis.com/css2?family=Montserrat:wght@400;600&display=swap">
<style>
  :root {
    --pink: #e34197;
    --charcoal: #3a3a3c;
    --ink: #1f1f21;
    --paper: #ffffff;
    --backdrop: #e9e9eb;
    --muted: #4a4a4d;
  }
  * { box-sizing: border-box; margin: 0; padding: 0; }
  html, body { width: 1200px; height: 900px; overflow: hidden; }
  body {
    background: var(--backdrop);
    font-family: "Montserrat", Arial, sans-serif;
    display: flex;
    flex-direction: column;
    align-items: center;
    justify-content: center;
    gap: 54px;
  }
  .card {
    position: relative;
    width: 640px;
    height: 366px;
    background: var(--paper);
    border-radius: 34px;
    overflow: hidden;
    box-shadow: 0 6px 18px rgba(0,0,0,0.12);
  }
  .card-art { position: absolute; inset: 0; width: 100%; height: 100%; }
  .wordmark {
    display: flex;
    align-items: center;
    gap: 10px;
    color: var(--ink);
    font-weight: 600;
    letter-spacing: -0.01em;
    white-space: nowrap;
  }
  .wordmark-dot {
    border-radius: 50%;
    background: var(--pink);
    flex: none;
  }
  .front .wordmark { position: absolute; left: 40px; top: 52px; font-size: 30px; }
  .front .wordmark-dot { width: 12px; height: 12px; }
  .holder {
    position: absolute;
    right: 44px;
    top: 44px;
    text-align: right;
    color: var(--paper);
  }
  .holder-name { font-size: 17px; font-weight: 600; letter-spacing: 0.08em; text-transform: uppercase; }
  .holder-title { font-size: 14px; font-weight: 400; margin-top: 4px; letter-spacing: 0.03em; }
  .contacts {
    position: absolute;
    left: 40px;
    top: 138px;
    list-style: none;
    display: flex;
    flex-direction: column;
    gap: 10px;
    font-size: 12.5px;
    color: var(--muted);
  }
  .contact { display: flex; align-items: center; gap: 10px; }
  .contact-icon { width: 16px; height: 16px; flex: none; }
  .back { display: flex; align-items: center; justify-content: center; }
  .back .wordmark { font-size: 64px; gap: 18px; }
  .back .wordmark-dot { width: 22px; height: 22px; }
</style>
</head>
<body>

<section class="card front" aria-label="Card front">
  <svg class="card-art" viewBox="0 0 640 366" aria-hidden="true">
    <path d="M240,0 H640 V238 C565,120 420,28 240,0 Z" fill="var(--charcoal)"/>
    <path d="M240,0 C420,28 565,120 640,238 V262 C560,140 420,34 240,0 Z" fill="var(--pink)"/>
  </svg>

  <div class="wordmark"><span class="wordmark-dot"></span>Staff Compass</div>

  <div class="holder">
    <p class="holder-name">Daniel Hartley</p>
    <p class="holder-title">Managing Director</p>
  </div>

  <ul class="contacts">
    <li class="contact">
      <svg class="contact-icon" viewBox="0 0 16 16"><circle cx="8" cy="8" r="8" fill="var(--pink)"/><path d="M5.5,4.5 l1.5,0 0.6,2 -1,0.8 a5,5 0 0 0 2,2 l0.8,-1 2,0.6 0,1.5 a1,1 0 0 1 -1,1 a6,6 0 0 1 -6,-6 a1,1 0 0 1 1,-1 z" fill="#fff"/></svg>
      <span>02 6555 0142</span>
    </li>
    <li class="contact">
      <svg class="contact-icon" viewBox="0 0 16 16"><circle cx="8" cy="8" r="8" fill="var(--pink)"/><rect x="5.5" y="3.5" width="5" height="9" rx="1" fill="#fff"/></svg>
      <span>0412 555 018</span>
    </li>
    <li class="contact">
      <svg class="contact-icon" viewBox="0 0 16 16"><circle cx="8" cy="8" r="8" fill="var(--pink)"/><rect x="4" y="5" width="8" height="6" fill="#fff"/><path d="M4,5 L8,8.5 L12,5" stroke="var(--pink)" fill="none"/></svg>
      <span>hello@staffcompass.com.au</span>
    </li>
    <li class="contact">
      <svg class="contact-icon" viewBox="0 0 16 16"><circle cx="8" cy="8" r="8" fill="var(--pink)"/><circle cx="8" cy="8" r="4" stroke="#fff" fill="none"/><path d="M4,8 H12 M8,4 V12" stroke="#fff"/></svg>
      <span>www.staffcompass.com.au</span>
    </li>
    <li class="contact">
      <svg class="contact-icon" viewBox="0 0 16 16"><circle cx="8" cy="8" r="8" fill="var(--pink)"/><path d="M8,13 C5,9 5,8 5,7 a3,3 0 0 1 6,0 c0,1 0,2 -3,6 z" fill="#fff"/></svg>
      <span>14 River Street, Port Macquarie NSW</span>
    </li>
  </ul>
</section>

<section class="card back" aria-label="Card back">
  <div class="wordmark"><span class="wordmark-dot"></span>Staff Compass</div>
</section>

</body>
</html>
```